Pavecrest Works

Im looking for something similar to (tarvalepaving.com) web site. I really want it to pop!
services we offer:
- Seal Coating
- Crack Filling
- Striping
- Asphalt
- Concrete
- Signage
- Road Grinding
- Grading
- Hydro Blasting
- Recycled asphalt
- Dumpster Pads
- Pressure Washing
- Wheel blocks
- Bollard installation
- Commercial Curbing
- Job site clean up
- Sweeping
- Forestry Clean up
- ADA Compliant work
- Speed bump installation and removal
- Snow removal
- Custom stair sets (Commercial)
Target Market(s)
Parking lot maintenance, asphalt repairs, road grading
Industry/Entity Type
construction, parking lot maintenance
Number of Pages Required
2 page

```html
<!DOCTYPE html>
<html lang="en">
<head>
<meta charset="utf-8">
<title>Pavecrest Works</title>
<link rel="stylesheet" href="https://fonts.googleapis.com/css2?family=Montserrat:wght@400;500;600;700;800&family=Raleway:wght@400;500;600;700&display=swap">
<style>
:root{
  --green:#80ee0a;
  --green-dark:#5fc400;
  --ink:#111111;
  --text:#333333;
  --muted:#555555;
  --line:#d6d6d6;
  --white:#ffffff;
  --black:#000000;
  --soft:#f2f2f2;
}
*{box-sizing:border-box;margin:0;padding:0}
html,body{width:1200px;height:3524px;overflow:hidden}
body{position:relative;background:var(--white);font-family:'Raleway',sans-serif;color:var(--text)}
.abs{position:absolute}
.btn{position:absolute;display:flex;align-items:center;justify-content:center;font-family:'Montserrat',sans-serif;font-weight:700;font-size:13px;letter-spacing:.3px;color:var(--ink);background:var(--green);text-transform:uppercase}
.btn--white{background:var(--white)}
.heading{position:absolute;left:0;width:1200px;text-align:center;font-family:'Montserrat',sans-serif;font-weight:700;font-size:34px;color:var(--ink)}
.heading span{color:var(--green);font-weight:500}
.rule{position:absolute;height:3px;width:50px;left:575px;background:var(--green)}
.rule--dark{background:var(--ink)}

/* top bar */
.topbar{left:0;top:0;width:1200px;height:30px;background:var(--green)}
.topbar__info{top:0;height:30px;display:flex;align-items:center;gap:6px;font-family:'Montserrat',sans-serif;font-size:12px;color:var(--ink)}
.topbar__info b{font-weight:700}
.topbar__phone{background:var(--ink);color:var(--white);padding:0 16px 0 22px;clip-path:polygon(12px 0,100% 0,100% 100%,0 100%)}
.logo-tab{left:0;top:0;width:330px;height:85px;background:var(--white);clip-path:polygon(104px 0,290px 0,310px 30px,310px 85px,0 85px,0 30px,92px 30px)}
.logo{font-family:'Montserrat',sans-serif;font-weight:700;color:var(--ink);line-height:1}
.logo__main{font-size:36px;letter-spacing:-.5px}
.logo__sub{font-size:14px;letter-spacing:9.5px;margin-top:2px}
.nav{top:30px;left:0;width:1200px;height:55px;background:var(--white)}
.nav__item{position:absolute;top:52px;font-family:'Montserrat',sans-serif;font-size:13px;font-weight:500;color:#555}
.nav__item--active{color:var(--green)}
.nav__bar{top:80px;left:596px;width:40px;height:4px;background:var(--green)}

/* hero */
.hero{left:0;top:85px;width:1200px;height:560px}
.hero__title{left:108px;top:240px;font-family:'Montserrat',sans-serif;font-weight:800;font-size:60px;letter-spacing:6px;color:var(--ink)}
.hero__sub{left:110px;top:320px;font-family:'Montserrat',sans-serif;font-weight:700;font-size:36px;color:var(--ink)}

/* about */
.about__lead{left:621px;top:770px;width:470px;font-size:16.5px;line-height:25px;font-weight:500;color:var(--ink)}
.about__body{left:621px;top:858px;width:470px;font-size:14.2px;line-height:23px;color:var(--muted)}

/* services */
.card{position:absolute;width:153px;height:143px;border:1.5px solid #cfcfcf;border-radius:4px;background:var(--white);display:flex;flex-direction:column;align-items:center}
.card--active{background:var(--green);border-color:var(--green);box-shadow:0 4px 10px rgba(0,0,0,.15)}
.card svg{margin-top:20px;width:62px;height:62px;fill:none;stroke:var(--green-dark);stroke-width:2.2;stroke-linecap:round;stroke-linejoin:round}
.card--active svg{stroke:var(--ink)}
.card__name{margin-top:14px;font-weight:700;font-size:14px;color:var(--ink)}

/* testimonials */
.quote{position:absolute;width:285px;height:274px;border:2px solid var(--green-dark);text-align:center}
.quote__text{margin:12px 10px 0;font-size:12.2px;line-height:19px;color:var(--ink);font-weight:500}
.quote__name{position:absolute;left:0;width:100%;top:216px;font-size:15px;font-weight:600;color:var(--ink)}
.quote__role{position:absolute;left:0;width:100%;top:240px;font-size:12px;font-style:italic;color:var(--ink)}
.qmark{position:absolute;font-family:'Montserrat',sans-serif;font-weight:800;font-size:64px;line-height:1;color:var(--ink)}
.dots{left:0;top:2305px;width:1200px;display:flex;justify-content:center;gap:7px}
.dots i{display:block;width:11px;height:11px;border-radius:50%;background:var(--white)}
.dots i:first-child{background:var(--ink)}

/* blog */
.post__img{position:absolute;width:308px;height:233px}
.post__box{position:absolute;width:273px;height:210px;background:var(--white);box-shadow:0 4px 14px rgba(0,0,0,.14);padding:32px 20px 0 22px}
.post__date{position:absolute;left:-19px;top:-15px;width:132px;height:35px;background:var(--green);display:flex;align-items:center;justify-content:center;font-family:'Montserrat',sans-serif;font-size:14px;font-weight:600;color:var(--ink)}
.post__title{font-size:17px;line-height:23px;font-weight:500;color:var(--ink)}
.post__excerpt{margin-top:10px;font-size:13.4px;line-height:21px;color:var(--muted)}
.post__link{margin-top:10px;display:inline-block;font-size:13px;font-weight:600;color:var(--ink);text-decoration:underline}

/* footer */
.footer__head{position:absolute;top:3238px;font-family:'Montserrat',sans-serif;font-weight:700;font-size:18px;color:var(--white)}
.footer__bar{position:absolute;top:3274px;width:38px;height:3px;background:var(--green)}
.footer__list{position:absolute;top:3294px;list-style:none;font-family:'Montserrat',sans-serif;font-size:12px;line-height:24px;color:#d0d0d0;text-transform:uppercase}
.footer__bottom{position:absolute;top:3469px;font-family:'Raleway',sans-serif;font-size:13.5px;color:var(--white)}
</style>
</head>
<body>

<!-- header -->
<div class="abs topbar"></div>
<div class="abs topbar__info" style="left:696px">
  <svg width="16" height="11" viewBox="0 0 16 11"><rect x="0.5" y="0.5" width="15" height="10" fill="none" stroke="#111"/><path d="M1 1l7 5 7-5" fill="none" stroke="#111"/></svg>
  Email <b>hello@pavecrestworks.com</b>
</div>
<div class="abs topbar__info topbar__phone" style="left:964px;width:236px">
  <svg width="16" height="16" viewBox="0 0 24 24"><path d="M6 3l3 4-2 2c1 3 4 6 7 7l2-2 4 3-2 4C10 21 3 14 3 5z" fill="none" stroke="#80ee0a" stroke-width="2"/></svg>
  Reach us <b>555 210 4480</b>
</div>
<div class="abs nav"></div>
<div class="abs logo-tab"></div>
<div class="abs logo" style="left:108px;top:13px">
  <div class="logo__main">PAVECREST</div>
  <div class="logo__sub">WORKS</div>
</div>
<div class="nav__item nav__item--active" style="left:594px">HOME</div>
<div class="nav__item" style="left:673px">ABOUT</div>
<div class="nav__item" style="left:760px">SERVICES</div>
<div class="nav__item" style="left:865px">BLOG</div>
<div class="abs nav__bar"></div>
<div class="btn" style="left:955px;top:37px;width:133px;height:42px">Contact us</div>

<!-- hero -->
<svg class="abs hero" viewBox="0 0 1200 560" role="img" aria-label="Tracked loader with a grading attachment working a gravel lot beside a green field">
  <defs>
    <linearGradient id="heroPhoto" x1="0" y1="0" x2="1" y2="1">
      <stop offset="0" stop-color="#b7c7d6"/>
      <stop offset=".45" stop-color="#8a7d63"/>
      <stop offset="1" stop-color="#6b5f4c"/>
    </linearGradient>
  </defs>
  <rect width="1200" height="560" fill="url(#heroPhoto)"/>
  <polygon points="0,0 562,0 398,560 0,560" fill="#80ee0a"/>
  <path d="M0,560 L0,545 C300,565 500,525 600,535 C800,550 1000,545 1200,560 Z" fill="#ffffff"/>
</svg>
<div class="abs hero__title">PAVECREST</div>
<div class="abs hero__sub">WORKS</div>
<div class="btn" style="left:111px;top:386px;width:133px;height:42px">Get started</div>
<div class="btn btn--white" style="left:253px;top:386px;width:131px;height:42px">Contact us</div>
<svg class="abs" style="left:22px;top:305px" width="60" height="60" viewBox="0 0 60 60"><circle cx="30" cy="30" r="29" fill="none" stroke="#111" stroke-width="1.2"/><path d="M39 30H21M27 24l-6 6 6 6" fill="none" stroke="#111" stroke-width="2"/></svg>
<svg class="abs" style="left:1132px;top:325px" width="24" height="20" viewBox="0 0 24 20"><path d="M3 10h17M14 4l6 6-6 6" fill="none" stroke="#111" stroke-width="2"/></svg>

<!-- about -->
<div class="abs" style="left:0;top:645px;width:1200px;height:544px;background:linear-gradient(180deg,#ffffff 0%,#f3f3f3 40%,#d8d8d8 100%)"></div>
<div class="abs" style="left:141px;top:739px;width:386px;height:360px;background:var(--green)"></div>
<div class="abs" role="img" aria-label="Yellow double drum roller parked on fresh asphalt" style="left:152px;top:726px;width:387px;height:362px;background:linear-gradient(180deg,#b9cbe0 0%,#8c9aa6 40%,#3b3e42 75%,#2c2e31 100%)"></div>
<div class="abs" style="left:621px;top:712px;font-family:'Montserrat',sans-serif;font-size:33px;font-weight:700;color:var(--ink)">About <span style="color:var(--green);font-weight:500">Us</span></div>
<p class="abs about__lead">Ioderspiciatis unde omnis iste natus error sit voluptatem accusantium doloremque laudantium, totam rem aperiameaque ipsa quaeab illo inventore.</p>
<p class="abs about__body">Perspiciatis unde omnis iste natus error sit voluptatem accusantium doloremque laudantium, totam rem aperiam, eaque ipsa quae ab illo inventore veritatis et quasi architecto beatae vitae dicta sunt explicabo. Nemo enim ipsam voluptatem quia voluptas sit aspernatur aut odit aut fugit, sed quia consequuntur magni dolores eos qui ratione voluptatem sequi nesciunt.</p>
<div class="btn" style="left:621px;top:1044px;width:148px;height:44px">Learn more</div>

<!-- services -->
<div class="heading" style="top:1260px">Our <span>Services</span></div>
<div class="rule" style="top:1312px"></div>

<div class="card" style="left:112px;top:1346px"><svg viewBox="0 0 64 64"><circle cx="22" cy="12" r="5"/><path d="M22 18l-6 18 8 8v14M18 36l-8 22M22 24l12 8M40 20l-6 28M30 50h14l-4 6z"/></svg><div class="card__name">Seal Coating</div></div>
<div class="card card--active" style="left:276px;top:1346px"><svg viewBox="0 0 64 64"><rect x="24" y="14" width="18" height="16"/><path d="M10 30h44v8H10z"/><circle cx="18" cy="46" r="8"/><rect x="34" y="40" width="22" height="14" rx="7"/></svg><div class="card__name">Crack Filling</div></div>
<div class="card" style="left:441px;top:1346px"><svg viewBox="0 0 64 64"><path d="M14 58L22 6h20l8 52zM32 10v8M32 26v8M32 42v8M20 22h24M18 34h28"/></svg><div class="card__name">Striping</div></div>
<div class="card" style="left:605px;top:1346px"><svg viewBox="0 0 64 64"><path d="M18 58s-12-14-12-24a12 12 0 0124 0c0 10-12 24-12 24z"/><circle cx="18" cy="34" r="4"/><path d="M48 30s-8-9-8-16a8 8 0 0116 0c0 7-8 16-8 16zM28 56l18-22" stroke-dasharray="4 4"/></svg><div class="card__name">Asphalt</div></div>
<div class="card" style="left:770px;top:1346px"><svg viewBox="0 0 64 64"><path d="M10 20l14-10 30 8-4 36-40-4z"/><circle cx="40" cy="32" r="6"/><path d="M18 36h10M22 44h14"/></svg><div class="card__name">Concrete</div></div>
<div class="card" style="left:934px;top:1346px"><svg viewBox="0 0 64 64"><path d="M6 58L32 14l26 44zM32 24v10M32 40v4M20 6l24 24M44 6L20 30"/></svg><div class="card__name">Signage</div></div>

<div class="card" style="left:112px;top:1508px"><svg viewBox="0 0 64 64"><path d="M8 58L16 6h32l8 52zM32 12v10M32 30v10M32 48v8M24 6l-4 52M40 6l4 52"/></svg><div class="card__name">Road Grinding</div></div>
<div class="card" style="left:276px;top:1508px"><svg viewBox="0 0 64 64"><path d="M34 6c-10 6-10 14 0 20s10 18-16 32M46 6c-10 6-10 14 0 20s10 18-16 32M40 12v4M40 28v6M34 44l-4 4"/></svg><div class="card__name">Grading</div></div>
<div class="card" style="left:441px;top:1508px"><svg viewBox="0 0 64 64"><path d="M16 10h26a8 8 0 010 16H22a8 8 0 000 16h24a8 8 0 010 16H16"/><circle cx="14" cy="10" r="4"/><circle cx="50" cy="58" r="4"/></svg><div class="card__name">Hydro Blasting</div></div>
<div class="card" style="left:605px;top:1508px"><svg viewBox="0 0 64 64"><path d="M8 46a24 24 0 0148 0M4 46h56v6H4zM26 22v-8h12v8M22 46V30M42 46V30M32 46V26"/></svg><div class="card__name">Recycled asphalt</div></div>
<div class="card" style="left:770px;top:1508px"><svg viewBox="0 0 64 64"><path d="M6 20l12-14 12 8-8 10zM18 6l12 30M30 36h18v12H30zM26 50h32v8H26z"/><circle cx="12" cy="52" r="6"/></svg><div class="card__name">Dumpster Pads</div></div>
<div class="card" style="left:934px;top:1508px"><svg viewBox="0 0 64 64"><path d="M36 6v34M26 40h20l4 18H22zM30 46v12M36 46v12M42 46v12M8 26h14v10H8zM10 44h12v12H10zM50 14l6-6M48 22h8"/></svg><div class="card__name">Pressure Washing</div></div>

<div class="btn" style="left:533px;top:1688px;width:133px;height:45px">View more</div>

<!-- testimonials -->
<div class="abs" role="img" aria-label="Green tinted backdrop of a parking structure" style="left:0;top:1819px;width:1200px;height:583px;background:linear-gradient(180deg,#78e400 0%,#80ee0a 55%,#86f00e 100%)"></div>
<div class="heading" style="top:1890px;font-size:32px">See What Our Customers Are Saying</div>
<div class="rule rule--dark" style="top:1941px"></div>

<div class="quote" style="left:118px;top:1986px">
  <p class="quote__text">Perspiciatis unde omnis iste natus error sit voluptatem accusantium doloremque laudantium, totam rem aperiam, eaque ipsa quae ab illo inventore veritatis et quasi architecto beatae vitae dicta sunt explicabo. Nemo enim ipsam voluptatem quia voluptas sit aspernatur aut odit aut fugit, sed quia consequuntur magni dolores eos qui ratione voluptatem sequi</p>
  <div class="quote__name">Daniel R Morrow</div>
  <div class="quote__role">Kelbrook, CEO</div>
</div>
<div class="quote" style="left:458px;top:1986px">
  <p class="quote__text">Perspiciatis unde omnis iste natus error sit voluptatem accusantium doloremque laudantium, totam rem aperiam, eaque ipsa quae ab illo inventore veritatis et quasi architecto beatae vitae dicta sunt explicabo. Nemo enim ipsam voluptatem quia voluptas sit aspernatur aut odit aut fugit, sed quia consequuntur magni dolores eos qui ratione voluptatem sequi</p>
  <div class="quote__name">Daniel R Morrow</div>
  <div class="quote__role">Kelbrook, CEO</div>
</div>
<div class="quote" style="left:800px;top:1986px">
  <p class="quote__text">Perspiciatis unde omnis iste natus error sit voluptatem accusantium doloremque laudantium, totam rem aperiam, eaque ipsa quae ab illo inventore veritatis et quasi architecto beatae vitae dicta sunt explicabo. Nemo enim ipsam voluptatem quia voluptas sit aspernatur aut odit aut fugit, sed quia consequuntur magni dolores eos qui ratione voluptatem sequi</p>
  <div class="quote__name">Daniel R Morrow</div>
  <div class="quote__role">Kelbrook, CEO</div>
</div>
<div class="qmark" style="left:92px;top:1994px">&ldquo;</div>
<div class="qmark" style="left:393px;top:2180px">&rdquo;</div>
<div class="qmark" style="left:433px;top:1994px">&ldquo;</div>
<div class="qmark" style="left:733px;top:2180px">&rdquo;</div>
<div class="qmark" style="left:774px;top:1994px">&ldquo;</div>
<div class="qmark" style="left:1073px;top:2180px">&rdquo;</div>
<div class="abs dots"><i></i><i></i><i></i><i></i><i></i><i></i><i></i></div>

<!-- blog -->
<div class="heading" style="top:2472px">Check Out <span>Our Blog</span></div>
<div class="rule" style="top:2520px"></div>

<div class="post__img" role="img" aria-label="Red brick crosswalk across an asphalt road" style="left:114px;top:2551px;background:linear-gradient(180deg,#aab6bf 0%,#6d6f70 35%,#9b3b2e 60%,#8a3327 100%)"></div>
<div class="post__img" role="img" aria-label="Skid steer grading a dirt path by trees" style="left:447px;top:2551px;background:linear-gradient(180deg,#c8d4dc 0%,#4f6d3a 40%,#5a5246 70%,#7c705e 100%)"></div>
<div class="post__img" role="img" aria-label="Worker sealing the floor of a parking garage" style="left:780px;top:2551px;background:linear-gradient(180deg,#8c949a 0%,#5d6267 45%,#2e3236 100%)"></div>

<div class="post__box" style="left:131px;top:2743px"><div class="post__date">May 21, 2021</div><div class="post__title">Ioderspiciatis unde omnis iste natus error</div><p class="post__excerpt">Perspiciatis unde omnis iste natus error sit voluptatem accusantium doloremque laudantium totam rem aperiam eaque ipsa quaeab</p><span class="post__link">Learn More</span></div>
<div class="post__box" style="left:464px;top:2743px"><div class="post__date">May 21, 2021</div><div class="post__title">Ioderspiciatis unde omnis iste natus error</div><p class="post__excerpt">Perspiciatis unde omnis iste natus error sit voluptatem accusantium doloremque laudantium totam rem aperiam eaque ipsa quaeab</p><span class="post__link">Learn More</span></div>
<div class="post__box" style="left:797px;top:2743px"><div class="post__date">May 21, 2021</div><div class="post__title">Ioderspiciatis unde omnis iste natus error</div><p class="post__excerpt">Perspiciatis unde omnis iste natus error sit voluptatem accusantium doloremque laudantium totam rem aperiam eaque ipsa quaeab</p><span class="post__link">Learn More</span></div>

<div class="btn" style="left:533px;top:3006px;width:133px;height:44px">View more</div>

<!-- footer -->
<svg class="abs" style="left:0;top:3126px" width="1200" height="398" viewBox="0 0 1200 398"><path d="M0,0 L600,30 L1200,4 L1200,398 L0,398 Z" fill="#000"/></svg>
<div class="abs logo" style="left:134px;top:3316px;color:var(--green)">
  <div class="logo__main" style="font-size:40px">PAVECREST</div>
  <div class="logo__sub" style="font-size:15px;letter-spacing:11px">WORKS</div>
</div>
<div class="footer__head" style="left:369px">QUICK LINKS</div>
<div class="footer__bar" style="left:369px"></div>
<ul class="footer__list" style="left:369px"><li>Home</li><li>About</li><li>Services</li><li>Blog</li><li>Contact us</li></ul>
<div class="footer__head" style="left:547px">LINKS</div>
<div class="footer__bar" style="left:547px"></div>
<ul class="footer__list" style="left:547px"><li>Copyright</li><li>Legal</li><li>Privacy</li><li>Accessibility</li><li>Sitemap</li></ul>
<div class="footer__head" style="left:696px">POLICY</div>
<div class="footer__bar" style="left:696px"></div>
<ul class="footer__list" style="left:696px"><li>Frequently asked questions</li><li>Terms &amp; conditions</li><li>Privacy policy</li><li>Site map</li><li>Cookies policy</li></ul>
<div class="footer__head" style="left:951px">SUPPORT</div>
<div class="footer__bar" style="left:951px"></div>
<ul class="footer__list" style="left:951px"><li>Team</li><li>About us</li><li>Careers</li><li>Our values</li></ul>

<div class="abs" style="left:109px;top:3431px;width:979px;height:1px;background:#333"></div>
<svg class="abs" style="left:1116px;top:3410px" width="44" height="44" viewBox="0 0 44 44"><circle cx="22" cy="22" r="22" fill="#80ee0a"/><path d="M16 25l6-6 6 6" fill="none" stroke="#111" stroke-width="2"/></svg>
<div class="footer__bottom" style="left:109px">Privacy Policy</div>
<div class="abs" style="left:219px;top:3463px;width:1px;height:26px;background:#fff"></div>
<div class="footer__bottom" style="left:241px">Terms of Use</div>
<div class="footer__bottom" style="left:790px;width:300px;text-align:right">©Copyrights. 2021 .All rights reserved</div>

</body>
</html>
```